Lorvex Tilo medical cannibis cultivation company

tag - Tilo rise
Lorvex Tilo medical cannabis cultivation - logo is selected- can we please see bold examples with our selection. We are mainly dealing with medical companies and professionals. We would like to be stand out in the crowd with our designs. Welcome any and all attempts. Thanks

Target Market(s)

Medical and Professional

Industry/Entity Type

Medical And Science

Font styles to use
Sans Serif

Colors

Designer to choose colors to be used in the design.

Requirements
Must have
• Bright colour and be bold- Love the teal and magenta that is currently on the dark background design.
Nice to have
• shading and the 3D affect- The shadowed appearance.
Should not have
• Anything related to illegal activity or un professional manners

```html
<!DOCTYPE html>
<html lang="en">
<head>
<meta charset="utf-8">
<title>Lorvex Tilo – Business Card</title>
<link rel="stylesheet" href="https://fonts.googleapis.com/css2?family=Roboto:wght@400;500;700&display=swap">
<style>
  :root {
    --stage: #6b6560;
    --card-light: #ffffff;
    --card-dark: #000000;
    --teal: #1aaee6;
    --magenta: #a1479f;
    --ring: #8c9196;
    --text-gray: #5f6163;
    --divider: #b9bbbd;
    --white: #ffffff;
  }
  * { box-sizing: border-box; margin: 0; padding: 0; }
  html, body { width: 1125px; height: 1200px; overflow: hidden; }
  body {
    background: var(--stage);
    font-family: "Roboto", Arial, sans-serif;
    position: relative;
  }
  .card {
    position: absolute;
    left: 150px;
    width: 825px;
    height: 470px;
    border-radius: 26px;
    box-shadow: 0 6px 18px rgba(0,0,0,0.35);
  }
  .card--front { top: 98px; background: var(--card-light); }
  .card--back { top: 632px; background: var(--card-dark); }

  /* front: brand block */
  .brand-ring {
    position: absolute;
    left: 163px; top: 110px;
    width: 170px; height: 170px;
    border: 5px solid var(--ring);
    border-radius: 50%;
  }
  .brand-name {
    position: absolute;
    left: 40px; width: 416px; top: 286px;
    text-align: center;
    font-size: 48px;
    line-height: 56px;
    font-weight: 500;
    color: var(--teal);
    letter-spacing: 0.5px;
  }
  .brand-tag {
    position: absolute;
    left: 96px; width: 304px; top: 340px;
    display: flex; align-items: center; gap: 10px;
    font-size: 21px;
    line-height: 24px;
    letter-spacing: 2px;
    color: var(--ring);
    text-transform: uppercase;
  }
  .brand-tag::before, .brand-tag::after {
    content: ""; flex: 1; height: 2px; background: var(--ring);
  }
  .divider {
    position: absolute;
    left: 450px; top: 93px;
    width: 2px; height: 288px;
    background: linear-gradient(to bottom, rgba(185,187,189,0), var(--divider) 15%, var(--divider) 85%, rgba(185,187,189,0));
  }

  /* front: contact block */
  .contact { position: absolute; left: 495px; top: 100px; }
  .contact__name {
    font-size: 29px; font-weight: 700; color: var(--teal);
    text-shadow: 0 2px 3px rgba(0,0,0,0.25);
    line-height: 36px;
  }
  .contact__title {
    font-size: 20px; font-weight: 500; color: var(--magenta);
    line-height: 24px;
  }
  .contact__address {
    margin-top: 16px;
    font-size: 19px; color: var(--text-gray);
    line-height: 25px;
  }
  .contact__list { list-style: none; margin-top: 14px; }
  .contact__item {
    display: flex; align-items: center; gap: 12px;
    font-size: 19px; color: var(--text-gray);
    height: 26.5px;
  }
  .contact__icon { width: 18px; height: 18px; fill: var(--teal); flex: none; }

  /* back */
  .back-ring {
    position: absolute;
    left: 279px; top: 96px;
    width: 268px; height: 268px;
    border: 6px solid var(--ring);
    border-radius: 50%;
  }
  .back-name {
    position: absolute;
    left: 0; width: 825px; top: 210px;
    text-align: center;
    font-size: 34px; line-height: 40px; font-weight: 500;
    color: var(--teal);
  }
  .back-web {
    position: absolute;
    left: 0; width: 825px; top: 404px;
    text-align: center;
    font-size: 19px;
    letter-spacing: 4.5px;
    color: var(--white);
  }
</style>
</head>
<body>

<section class="card card--front">
  <div class="brand-ring"></div>
  <div class="brand-name">LORVEX TILO</div>
  <div class="brand-tag">Tilo rise</div>

  <div class="divider"></div>

  <div class="contact">
    <div class="contact__name">MAREN ODELL</div>
    <div class="contact__title">CEO/FOUNDER</div>
    <div class="contact__address">4216 Fernhill Road<br>Juneau, Alaska 29813</div>
    <ul class="contact__list">
      <li class="contact__item">
        <svg class="contact__icon" viewBox="0 0 24 24"><path d="M6.6 10.8a15.1 15.1 0 0 0 6.6 6.6l2.2-2.2c.3-.3.7-.4 1-.2 1.1.4 2.3.6 3.6.6.6 0 1 .4 1 1V20c0 .6-.4 1-1 1A17 17 0 0 1 3 4c0-.6.4-1 1-1h3.5c.6 0 1 .4 1 1 0 1.3.2 2.5.6 3.6.1.3 0 .7-.2 1z"/></svg>
        614 205 7381
      </li>
      <li class="contact__item">
        <svg class="contact__icon" viewBox="0 0 24 24"><path d="M7 1h10a2 2 0 0 1 2 2v18a2 2 0 0 1-2 2H7a2 2 0 0 1-2-2V3a2 2 0 0 1 2-2zm0 3v14h10V4zm5 15.5a1.2 1.2 0 1 0 0 2.4 1.2 1.2 0 0 0 0-2.4z"/></svg>
        729 380 5146
      </li>
      <li class="contact__item">
        <svg class="contact__icon" viewBox="0 0 24 24"><path d="M6 2h12v5H6zM3 8h18a2 2 0 0 1 2 2v7h-4v5H5v-5H1v-7a2 2 0 0 1 2-2zm4 7v5h10v-5z"/></svg>
        357 912 6048
      </li>
      <li class="contact__item">
        <svg class="contact__icon" viewBox="0 0 24 24"><path d="M2 5h20v14H2zm2 2v.5l8 5.5 8-5.5V7zm0 3v7h16v-7l-8 5.5z"/></svg>
        maren@lorvextilo.com
      </li>
      <li class="contact__item">
        <svg class="contact__icon" viewBox="0 0 24 24"><circle cx="12" cy="12" r="10"/></svg>
        www.lorvextilo.com
      </li>
    </ul>
  </div>
</section>

<section class="card card--back">
  <div class="back-ring"></div>
  <div class="back-name">LORVEX TILO</div>
  <div class="back-web">www.lorvextilorise.com</div>
</section>

</body>
</html>
```